Corporate Business Card

Very professional, Modern, Not to busy, include phone address email, website
(253) 617-4930, 18761 52nd Avenue S, Kent, WA 98047, martin@plumlinegroup.com, varkoworks.com

Target Market(s)

Manufacturing

Industry/Entity Type

Aero, machining, manufacturing, Off road racing

Contact Information for Business Card

Phone, address email, website

```html
<!DOCTYPE html>
<html lang="en">
<head>
<meta charset="utf-8">
<title>Varko Works – Business Card</title>
<link rel="stylesheet" href="https://fonts.googleapis.com/css2?family=Lato:wght@400;700;900&display=swap">
<style>
  :root {
    --backdrop: #2b2b2b;
    --brand-red: #d2232a;
    --brand-navy: #17356d;
    --paper: #ffffff;
  }
  * { margin: 0; padding: 0; box-sizing: border-box; }
  html, body { width: 1200px; height: 1200px; overflow: hidden; }
  body {
    background: var(--backdrop);
    font-family: "Lato", Arial, sans-serif;
    position: relative;
  }
  .card {
    position: absolute;
    left: 250px;
    width: 700px;
    height: 400px;
    overflow: hidden;
  }
  .card--front { top: 170px; background: var(--paper); }
  .card--back  { top: 631px; background: var(--brand-red); }

  .front-panels { position: absolute; left: 0; top: 0; }

  .identity {
    position: absolute;
    left: 40px;
    top: 60px;
    color: var(--paper);
  }
  .identity__name {
    font-weight: 700;
    font-size: 29px;
    letter-spacing: 0.2px;
    line-height: 1;
  }
  .identity__title {
    font-weight: 400;
    font-size: 19px;
    margin-top: 6px;
    letter-spacing: 0.3px;
  }

  .contacts {
    position: absolute;
    left: 42px;
    top: 222px;
    list-style: none;
    color: var(--paper);
    font-size: 17px;
    letter-spacing: 0.3px;
  }
  .contacts__item {
    display: flex;
    align-items: flex-start;
    line-height: 23.5px;
  }
  .contacts__item + .contacts__item { margin-top: 0; }
  .contacts__item--address { margin-bottom: 12px; }
  .contacts__icon {
    width: 14px;
    height: 14px;
    margin-top: 5px;
    margin-right: 13px;
    flex: none;
  }

  .brand-name {
    position: absolute;
    font-weight: 900;
    letter-spacing: 2px;
    white-space: nowrap;
    text-transform: uppercase;
  }
  .brand-name--front {
    left: 328px;
    width: 372px;
    top: 178px;
    text-align: center;
    font-size: 40px;
    color: var(--brand-navy);
  }
  .brand-name--back {
    left: 0;
    width: 700px;
    top: 165px;
    text-align: center;
    font-size: 62px;
    color: var(--paper);
  }
</style>
</head>
<body>

<section class="card card--front" aria-label="Business card front">
  <svg class="front-panels" width="700" height="400" viewBox="0 0 700 400" aria-hidden="true">
    <polygon points="0,0 328,0 328,125 289,164 0,164" fill="var(--brand-red)"/>
    <polygon points="0,167 289,167 328,205 328,400 0,400" fill="var(--brand-navy)"/>
  </svg>

  <div class="identity">
    <h1 class="identity__name">DANIEL REYES</h1>
    <p class="identity__title">Managing Director</p>
  </div>

  <ul class="contacts">
    <li class="contacts__item contacts__item--address">
      <svg class="contacts__icon" viewBox="0 0 14 14" aria-hidden="true">
        <path d="M7 0.5a4.6 4.6 0 0 0-4.6 4.6C2.4 8.6 7 13.5 7 13.5s4.6-4.9 4.6-8.4A4.6 4.6 0 0 0 7 0.5z" fill="#fff"/>
        <circle cx="7" cy="5" r="1.7" fill="var(--brand-navy)"/>
      </svg>
      <span>18761 52nd Avenue S<br>Kent, WA 98047</span>
    </li>
    <li class="contacts__item">
      <svg class="contacts__icon" viewBox="0 0 14 14" aria-hidden="true">
        <path d="M3 1.5l2 2.6-1.2 1.5c.8 1.7 2 2.9 3.6 3.7l1.5-1.2 2.6 2-1.1 2.2C6 12 2 8 1.7 2.6z" fill="#fff"/>
        <path d="M8 1.5a4.5 4.5 0 0 1 4.5 4.5M8 3.7A2.3 2.3 0 0 1 10.3 6" stroke="#fff" stroke-width="1.1" fill="none"/>
      </svg>
      <span>(253) 617-4930</span>
    </li>
    <li class="contacts__item">
      <svg class="contacts__icon" viewBox="0 0 14 14" aria-hidden="true">
        <rect x="1" y="3" width="12" height="8.5" fill="#fff"/>
        <path d="M1 3l6 4.6L13 3" stroke="var(--brand-navy)" stroke-width="1.1" fill="none"/>
      </svg>
      <span>martin@plumlinegroup.com</span>
    </li>
    <li class="contacts__item">
      <svg class="contacts__icon" viewBox="0 0 14 14" aria-hidden="true">
        <circle cx="7" cy="7" r="6" fill="#fff"/>
        <path d="M4 4.5c1 .2 1.6 1 1.3 2-.3.8.6 1.4.4 2.6M9 2.8c-.6 1-.1 2 1 2.2.9.2 1.3 1.2.9 2" stroke="var(--brand-navy)" stroke-width="1.2" fill="none"/>
      </svg>
      <span>www.varkoworks.com</span>
    </li>
  </ul>

  <p class="brand-name brand-name--front">Varko Works</p>
</section>

<section class="card card--back" aria-label="Business card back">
  <p class="brand-name brand-name--back">Varko Works</p>
</section>

</body>
</html>
```